Maple Gable Business Card

Colors can be blue, grey and white as you see in the attached logo. Needs to have a spot for name, title, phone, email, address, and website. There also needs to be a spot for an agent's picture.

Contact Information for Business Card

See project description.

Colors

Designer to choose colors to be used in the design.

```html
<!DOCTYPE html>
<html lang="en">
<head>
<meta charset="utf-8">
<title>Maple Gable Business Card</title>
<link href="https://fonts.googleapis.com/css2?family=Montserrat:wght@400;500;600;700&family=Oswald:wght@600&display=swap" rel="stylesheet">
<style>
  :root {
    --stage: #2a2a2c;
    --paper: #ffffff;
    --brand-blue: #2f7cc4;
    --ink-grey: #5a5a5c;
    --photo-tone-a: #d9dde2;
    --photo-tone-b: #b9c1cb;
    --back-grey: #444446;
    --back-grey-light: #4f4f52;
  }
  * { box-sizing: border-box; margin: 0; padding: 0; }
  html, body { width: 1200px; height: 900px; overflow: hidden; }
  body {
    background: var(--stage);
    font-family: "Montserrat", sans-serif;
    display: flex;
    flex-direction: column;
    align-items: center;
    justify-content: center;
    gap: 56px;
  }
  .card {
    width: 630px;
    height: 360px;
    position: relative;
    border-radius: 3px;
    overflow: hidden;
  }
  /* Front */
  .card-front { background: var(--paper); color: var(--ink-grey); }
  .agent-photo {
    position: absolute;
    left: 52px;
    top: 36px;
    width: 92px;
    height: 92px;
    border-radius: 50%;
    background: linear-gradient(160deg, var(--photo-tone-a), var(--photo-tone-b));
    border: 3px solid var(--brand-blue);
  }
  .brand-front {
    position: absolute;
    top: 60px;
    right: 60px;
    display: flex;
    align-items: center;
    gap: 14px;
  }
  .brand-square { width: 24px; height: 24px; background: var(--brand-blue); }
  .brand-name {
    font-weight: 600;
    font-size: 32px;
    letter-spacing: 1px;
    text-transform: uppercase;
    white-space: nowrap;
    color: var(--brand-blue);
  }
  .agent {
    position: absolute;
    left: 40px;
    top: 156px;
    width: 250px;
    text-align: right;
  }
  .agent-name {
    font-family: "Oswald", sans-serif;
    font-weight: 600;
    font-size: 36px;
    line-height: 1;
    white-space: nowrap;
    color: var(--brand-blue);
    text-transform: uppercase;
  }
  .agent-title { font-size: 15px; margin-top: 8px; }
  .divider {
    position: absolute;
    left: 308px;
    top: 152px;
    width: 1.5px;
    height: 90px;
    background: var(--brand-blue);
  }
  .contacts {
    position: absolute;
    left: 328px;
    top: 152px;
    list-style: none;
    font-size: 16px;
    line-height: 30px;
    white-space: nowrap;
  }
  .contacts li { display: flex; align-items: center; gap: 10px; }
  .contacts svg { width: 13px; height: 13px; fill: none; stroke: var(--brand-blue); stroke-width: 2; }
  .address {
    position: absolute;
    left: 52px;
    bottom: 46px;
    font-size: 16px;
    white-space: nowrap;
  }
  /* Back */
  .card-back {
    background: linear-gradient(135deg, var(--back-grey-light), var(--back-grey));
    display: flex;
    align-items: center;
    justify-content: center;
  }
  .brand-back .brand-name { color: var(--paper); font-size: 40px; }
</style>
</head>
<body>
  <section class="card card-front" aria-label="Business card front">
    <div class="agent-photo" role="img" aria-label="Agent portrait photo"></div>
    <div class="brand-front">
      <span class="brand-square"></span>
      <span class="brand-name">Maple Gable</span>
    </div>
    <div class="agent">
      <p class="agent-name">Daniel Harper</p>
      <p class="agent-title">Director</p>
    </div>
    <div class="divider"></div>
    <ul class="contacts">
      <li>
        <svg viewBox="0 0 14 14"><path d="M3 1.5l2 3-1.3 1.3a7 7 0 0 0 4.5 4.5L9.5 9l3 2-1.2 1.8C6 13 1 8 1.2 2.7z"/></svg>
        555 214-3067
      </li>
      <li>
        <svg viewBox="0 0 14 14"><rect x="1.5" y="3" width="11" height="8"/><path d="M1.5 3l5.5 4.5L12.5 3"/></svg>
        hello@maplegable.com
      </li>
      <li>
        <svg viewBox="0 0 14 14"><circle cx="7" cy="7" r="5.5"/><path d="M1.5 7h11M7 1.5c-3 3.5-3 7.5 0 11M7 1.5c3 3.5 3 7.5 0 11"/></svg>
        www.maplegable.com
      </li>
    </ul>
    <p class="address">48 Linden Avenue Hartwell, MA 02190</p>
  </section>

  <section class="card card-back" role="img" aria-label="Business card back with a faint repeating brand pattern on dark grey">
    <div class="brand-back">
      <span class="brand-name">Maple Gable</span>
    </div>
  </section>
</body>
</html>
```